Buchcover zum Thema Hausverwalter
Zielgruppe
Ich bin Autor und schreibe ein Buch über Hausverwalter.
Die Autoren sind Lorenz Waltl und Gottfried Waltl.
Der Verlag ist hollmeier & traunsteg.
Der Titel lautet: 'Mietparteien am Küchentisch - Seltsame Begebenheiten aus dem Altbau durch die Jahrzehnte'.
In diesem Buch geht es um den Beruf des Hausverwalters.
Es handelt sich um lustige Geschichten. Wir haben knapp 50 Hausverwalter aus Wien und Umgebung interviewt und von Mietern und Eigentümern die lustigsten und kuriosesten Geschichten erfahren. Es sind verrückte Sachen dabei.
Intro:
Der Hausverwalter weiß nie, was ihm der neue Arbeitstag bringen wird: überschwemmte Garagen mit schwimmenden Luxusautos, nervenaufreibende Eigentümer:innenversammlungen oder „nackerte“ Einbrecher. So unterschiedlich die Hausverwalter:innen, so unterschiedlich ihre Erinnerungen.
In seiner wechselhaften Geschichte hat der Berufsstand viel erlebt: mit Schwarzgeld gefüllte Safes oder marode Zinshäuser, oft stand er mit einem Fuß im sprichwörtlichen Kriminal. Alles vorbei. Heute stellen Dekarbonisierung und Digitalisierung den modernen und die moderne Hausverwalterin vor neue Herausforderungen.
Ich brauche ein tolles Buch Cover dafür!
Aufgabenstellung
Das Buch kommt in den österreichischen und deutschen Handel und soll ein Mega tolles Cover haben, wo Leute gerne hin greifen
So in die Richtung aber heller und freundlicher.
https://www.bildtafel-beispiel.de/pin/book-cover-design-of-the-lantern-by-the-pond--804417362950218/
https://www.bildtafel-beispiel.de/pin/47019362588204516/
https://www.bildtafel-beispiel.de/pin/629401857730415268/
https://www.bildtafel-beispiel.de/pin/317785062449138057/

```html
<!DOCTYPE html>
<html lang="de">
<head>
<meta charset="utf-8">
<title>Mietparteien am Küchentisch – Buchcover</title>
<link rel="stylesheet" href="https://fonts.googleapis.com/css2?family=Jost:wght@400;500;700&display=swap">
<style>
  :root {
    --stage: #8b8c8e;
    --yellow: #ffcc00;
    --orange: #f9b800;
    --grey-base: #dcdcde;
    --grey-light: #ececed;
    --grey-dark: #c9c9cb;
    --ink-dark: #3a3a3c;
    --ink-mid: #6c6c6e;
    --ink-soft: #59595b;
    --ink-black: #111111;
  }
  html, body {
    margin: 0;
    padding: 0;
    width: 1200px;
    height: 2399px;
    overflow: hidden;
    background: var(--stage);
  }
  .canvas {
    position: relative;
    width: 1200px;
    height: 2399px;
  }
  .book-cover {
    position: absolute;
    left: 100px;
    top: 403px;
    width: 1000px;
    height: 1593px;
    display: block;
    font-family: "Jost", sans-serif;
  }
  .authors { font-size: 28px; font-weight: 400; fill: var(--ink-black); letter-spacing: 0.2px; }
  .title-main { font-size: 84px; font-weight: 700; fill: var(--ink-dark); }
  .title-sub { font-size: 60px; font-weight: 700; fill: var(--ink-mid); }
  .subtitle { font-size: 25px; font-weight: 400; fill: var(--ink-soft); }
  .publisher { font-size: 25px; font-weight: 500; fill: var(--ink-soft); font-variant: small-caps; letter-spacing: 0.3px; }
</style>
</head>
<body>
<div class="canvas">
  <svg class="book-cover" viewBox="0 0 702 1118" xmlns="http://www.w3.org/2000/svg">
    <defs>
      <linearGradient id="facade-tones" x1="0" y1="0" x2="1" y2="1">
        <stop offset="0" stop-color="#8e8e90"/>
        <stop offset="0.5" stop-color="#5a5a5c"/>
        <stop offset="1" stop-color="#3a3a3c"/>
      </linearGradient>
      <linearGradient id="skyline-tones" x1="0" y1="0" x2="0" y2="1">
        <stop offset="0" stop-color="#c4c4c6" stop-opacity="0.7"/>
        <stop offset="1" stop-color="#cfcfd1" stop-opacity="0.5"/>
      </linearGradient>
      <clipPath id="cover-clip"><rect width="702" height="1118"/></clipPath>
    </defs>

    <g clip-path="url(#cover-clip)">
      <rect class="field-yellow" width="702" height="1118" fill="var(--yellow)"/>
      <polygon class="band-orange" points="0,100 702,355 0,610" fill="var(--orange)"/>
      <polygon class="field-grey" points="0,610 702,355 702,1118 0,1118" fill="var(--grey-base)"/>
      <polygon class="band-grey-light" points="147,950 702,750 702,1118 580,1118" fill="var(--grey-light)"/>
      <polygon class="band-grey-dark" points="0,930 587,1118 0,1118" fill="var(--grey-dark)"/>

      <rect class="skyline" x="357" y="830" width="335" height="288" fill="url(#skyline-tones)"
            role="img" aria-label="Blasse Silhouette zweier Wohnhochhäuser"/>

      <circle class="facade-photo" cx="287" cy="377" r="252" fill="url(#facade-tones)"
              role="img" aria-label="Schwarzweißfoto einer gestreiften Hausfassade mit kleiner Figur davor"/>

      <text class="authors" x="647" y="100" text-anchor="end">LORENZ WALTL &amp;</text>
      <text class="authors" x="647" y="137" text-anchor="end">GOTTFRIED WALTL</text>

      <text class="title-main" x="355" y="680" text-anchor="middle" transform="rotate(-20 355 680)">MIETPARTEIEN</text>
      <text class="title-sub" x="412" y="727" text-anchor="middle" transform="rotate(-20 412 727)">AM KÜCHENTISCH</text>
      <text class="subtitle" x="424" y="784" text-anchor="middle" transform="rotate(-20 424 784)">Seltsame Begebenheiten aus dem Altbau</text>
      <text class="subtitle" x="441" y="816" text-anchor="middle" transform="rotate(-20 441 816)">durch die Jahrzehnte</text>

      <text class="publisher" x="69" y="1052">Hollmeier &amp; Traunsteg</text>
    </g>
  </svg>
</div>
</body>
</html>
```